Quorva - corporate Business Card

We need a good look and innovative business card for a new start up company based in Los Angeles called "Quorva". We are in a payment business, including payment card, app, and ewallet. We are expert in online payment and Card not present (CNP) transaction.
We need an innovative, modern business card.

Our logo font is Aero Matics

Target Market(s)

Startup - Bank - Online Payment - Card Manufacturing

Industry/Entity Type

Startup

Contact Information for Business Card

phone: 555 014 7396 - Address: 4172 Marlowe blvd, Brenmoor, NV 89014

Requirements
Must have
• Message: innovative, professional, expert, high tech, trust, online payment expert, security
Nice to have
• no comment
Should not have
• no Comment

```html
<!DOCTYPE html>
<html lang="en">
<head>
<meta charset="utf-8">
<title>Quorva – Business Card</title>
<link href="https://fonts.googleapis.com/css2?family=Montserrat:wght@600;700;800&family=Nunito+Sans:wght@400;600&display=swap" rel="stylesheet">
<style>
  :root {
    --brand-red: #b81f2e;
    --tint-red: #f7e3e5;
    --paper: #ffffff;
    --ink-grey: #5e5e62;
    --backdrop: #e9e9ec;
  }
  * { box-sizing: border-box; margin: 0; padding: 0; }
  html, body { width: 1200px; height: 900px; overflow: hidden; }
  body {
    background: var(--backdrop);
    font-family: "Nunito Sans", Arial, sans-serif;
    display: flex;
    flex-direction: column;
    align-items: center;
    justify-content: center;
    gap: 60px;
  }
  .card {
    position: relative;
    width: 630px;
    height: 360px;
    border-radius: 22px;
    overflow: hidden;
    box-shadow: 0 14px 30px rgba(0,0,0,0.18);
  }

  /* Front */
  .card-front {
    background: var(--brand-red);
    display: flex;
    align-items: center;
    justify-content: center;
    gap: 24px;
  }
  .brand-dot {
    width: 120px;
    height: 120px;
    border-radius: 50%;
    background: var(--paper);
  }
  .brand-name {
    font-family: "Montserrat", Arial, sans-serif;
    font-weight: 700;
    font-size: 92px;
    letter-spacing: 1px;
    color: var(--paper);
    line-height: 1;
  }

  /* Back */
  .card-back { background: var(--paper); }
  .back-disc {
    position: absolute;
    left: 200px;
    top: 20px;
    width: 300px;
    height: 300px;
    border-radius: 50%;
    background: var(--tint-red);
  }
  .holder {
    position: absolute;
    right: 340px;
    top: 176px;
    text-align: right;
  }
  .holder-name {
    font-family: "Montserrat", Arial, sans-serif;
    font-weight: 800;
    font-size: 25px;
    color: var(--brand-red);
    white-space: nowrap;
  }
  .holder-role {
    font-size: 16px;
    color: var(--ink-grey);
    margin-top: 2px;
  }
  .contacts {
    position: absolute;
    left: 348px;
    top: 102px;
    list-style: none;
  }
  .contacts li {
    display: flex;
    align-items: center;
    gap: 10px;
    font-size: 16px;
    letter-spacing: 0.5px;
    color: var(--ink-grey);
    height: 27px;
  }
  .contacts svg { width: 13px; height: 13px; fill: var(--brand-red); flex: none; }
  .address-band {
    position: absolute;
    left: 0;
    right: 0;
    bottom: 0;
    height: 34px;
    background: var(--brand-red);
  }
  .address {
    position: absolute;
    left: 112px;
    bottom: 6px;
    padding: 2px 12px;
    border: 2px solid var(--paper);
    border-radius: 3px;
    font-size: 15px;
    font-weight: 600;
    letter-spacing: 0.4px;
    color: var(--paper);
    background: var(--brand-red);
    white-space: nowrap;
  }
</style>
</head>
<body>

  <section class="card card-front" aria-label="Card front">
    <span class="brand-dot"></span>
    <span class="brand-name">Quorva</span>
  </section>

  <section class="card card-back" aria-label="Card back">
    <span class="back-disc"></span>

    <div class="holder">
      <p class="holder-name">Dana Whitfield</p>
      <p class="holder-role">President</p>
    </div>

    <ul class="contacts">
      <li>
        <svg viewBox="0 0 24 24" aria-hidden="true"><path d="M6.6 10.8a15.1 15.1 0 0 0 6.6 6.6l2.2-2.2a1 1 0 0 1 1-.25 11.4 11.4 0 0 0 3.6.57 1 1 0 0 1 1 1V20a1 1 0 0 1-1 1A17 17 0 0 1 3 4a1 1 0 0 1 1-1h3.5a1 1 0 0 1 1 1c0 1.25.2 2.45.57 3.57a1 1 0 0 1-.25 1z"/></svg>
        555 014 7396
      </li>
      <li>
        <svg viewBox="0 0 24 24" aria-hidden="true"><path d="M2 5h20v14H2z"/><path d="M3 6l9 6.5L21 6" fill="none" stroke="#fff" stroke-width="1.8"/></svg>
        dana@quorva.com
      </li>
      <li>
        <svg viewBox="0 0 24 24" aria-hidden="true"><circle cx="12" cy="12" r="10" fill="none" stroke="#b81f2e" stroke-width="2.4"/><path d="M2 12h20M12 2c3 3 4 6.5 4 10s-1 7-4 10c-3-3-4-6.5-4-10s1-7 4-10z" fill="none" stroke="#b81f2e" stroke-width="2"/></svg>
        www.quorva.com
      </li>
    </ul>

    <div class="address-band">
      <p class="address">4172 Marlowe blvd, Brenmoor, NV 89014</p>
    </div>
  </section>

</body>
</html>
```